QRV Advisors needs a web site

We need a web site for www.qrvadvisors-example.com. QRV is a mergers and acquisition consulting company that focuses our buyer and seller services on logistics companies. We help put companies together, and help with legal and financial due diligence. We want the web site to express our service and show the logistics components. We want personalized images versus pictures of trucks and airplanes.

Our new logo uses Burgandy and grey colors. Image attached. We are not in to bold, big letters...classy, artistic, low key preferred. Confidentiality, experience, professional are what we want to express on the site.

All we expect for the first part of this project is a home page, and one subpage.  We are budgeting other funds for the technical aspects of the web site

Reason: All that I'm seeing so far is trucks, forklifts and planes. We are a legal mergers and acquisitions firm that focus on logistics. I like some of the images to say logistics, but really want it say legal, financial, and putting companies together. Will pay extra for the sub page if someone can impress us with a home page.

Reason: Swamped with another project at the moment...will work on this over the weekend and provide designer feedback and select final design by Tuesday

```html
<!DOCTYPE html>
<html lang="en">
<head>
<meta charset="utf-8">
<title>QRV Advisors — Home</title>
<link rel="stylesheet" href="https://fonts.googleapis.com/css2?family=Ubuntu:wght@400;500&display=swap">
<style>
:root{
  --burgundy:#a6093d;
  --burgundy-bright:#de004b;
  --grey-dark:#3a3a3a;
  --grey-mid:#6b6b6b;
  --grey-text:#333;
  --panel:#f5f4f4;
  --line:#d9d9d9;
  --footer:#343434;
  --footer-edge:#5b4b45;
  --white:#fff;
}
*{box-sizing:border-box;margin:0;padding:0}
html,body{width:1174px;height:1200px;overflow:hidden}
body{font-family:"Ubuntu",sans-serif;color:var(--grey-text);background:var(--white);position:relative}
.abs{position:absolute}

/* header */
.site-header{left:0;top:0;width:1174px;height:103px;background:linear-gradient(#fff,#ececec)}
.brand{left:121px;top:30px;display:flex;align-items:center;gap:12px}
.brand-mark{width:14px;height:14px;background:var(--burgundy)}
.brand-name{font-size:34px;font-weight:500;color:var(--burgundy);letter-spacing:1px}
.phone{left:877px;top:38px;display:flex;align-items:center;gap:12px;font-size:23px;color:var(--burgundy)}

/* nav */
.main-nav{left:0;top:103px;width:1174px;height:50px;background:var(--burgundy)}
.nav-list{list-style:none;position:absolute;left:123px;top:0;height:50px;display:flex}
.nav-list li{height:50px;line-height:50px;padding:0 11px;color:#fff;font-size:18px;border-right:1px solid rgba(0,0,0,.18)}
.nav-list li.current{background:#fff;color:var(--burgundy);width:91px;text-align:center}
.search{left:827px;top:9px;width:214px;height:28px;background:var(--burgundy-bright);color:#fff;font-size:14px;padding:6px 11px}
.search svg{position:absolute;right:8px;top:6px}

/* hero */
.hero{left:0;top:153px;width:1174px;height:336px;background:linear-gradient(100deg,#6b5d55 0%,#c9c2b6 35%,#e9e6df 55%,#8b8580 80%,#4a4038 100%)}
.hero-caption{left:0;top:289px;width:1174px;height:47px;background:rgba(25,25,25,.82);color:#fff;font-size:21px;padding:11px 131px}
.dots{right:133px;top:17px;display:flex;gap:9px}
.dots span{width:11px;height:11px;border-radius:50%;background:#fff}
.dots span.on{background:var(--burgundy)}

/* body backdrop */
.backdrop{left:0;top:489px;width:1174px;height:543px;background:linear-gradient(90deg,#767b80,#b6bcc1 6%,#8c9196 10%,#a8adb2 90%,#c4c8cc 95%,#7c8186)}
.content{left:121px;top:489px;width:932px;height:543px;background:#fff}

.services{left:304px;top:483px;width:565px;height:83px;border-radius:0 0 10px 10px;background:linear-gradient(#fafafa,#dedede);box-shadow:0 2px 4px rgba(0,0,0,.25);display:flex;align-items:center}
.service{display:flex;align-items:center;gap:8px;height:60px;padding:0 10px;border-right:1px solid #c9c9c9}
.service:last-child{border-right:0}
.service-title{color:var(--burgundy);font-size:18px;line-height:20px;font-weight:500}

.box{top:614px;width:296px;height:299px;background:var(--panel);border:1px solid #e3e3e3}
.box-head{position:absolute;left:53px;top:-5px;width:186px;height:31px;background:var(--burgundy);color:#fff;font-size:17px;font-weight:500;text-align:center;line-height:31px;border-radius:0 0 3px 3px}
.btn-dark{position:absolute;right:14px;bottom:-6px;background:var(--grey-dark);color:#fff;font-size:13px;padding:3px 9px;border-radius:6px 6px 0 0}

.mission-photo{position:absolute;left:11px;top:47px;width:268px;height:92px;border:3px solid #fff;outline:1px solid #ddd;background:linear-gradient(90deg,#54493f,#d8cdbf 40%,#c8b8a2 60%,#3f3a3a)}
.mission-text{position:absolute;left:16px;top:155px;width:262px;font-size:12.5px;line-height:18.3px}

.news-item{position:absolute;left:13px;width:272px;display:flex;gap:14px;padding-bottom:12px;border-bottom:1px solid var(--line)}
.news-item:last-child{border-bottom:0}
.date{width:33px;flex:none;text-align:center;background:#dcdcdc;color:var(--grey-dark);font-size:16px;line-height:22px}
.date b{display:block;background:var(--grey-dark);color:#fff;font-size:12px;font-weight:400;line-height:16px}
.news-title{font-size:13.5px;color:#222;margin-bottom:2px}
.news-body{font-size:12px;line-height:16.3px}

.field{position:absolute;left:19px;font-size:13.5px}
.input{position:absolute;left:85px;width:187px;height:21px;background:#fff;border:1px solid #ccc}

.partners{left:121px;top:913px;width:932px;height:119px;display:flex;align-items:center;justify-content:space-around;padding:0 70px}
.partner{font-size:23px;font-weight:500;color:#4a4a4a}
.arrow{top:965px}

/* footer */
.site-footer{left:0;top:1032px;width:1174px;height:168px;background:var(--footer);border-top:5px solid var(--footer-edge);color:#fff}
.f-col h3{font-size:18px;font-weight:400;margin-bottom:12px}
.f-col ul{list-style:none;font-size:13.5px;line-height:19.5px}
.f-col p{font-size:12.5px;line-height:16px;color:#ddd}
.email{margin-top:12px;width:201px;height:23px;background:#fff;border-radius:2px;color:#888;font-size:12.5px;padding:3px 9px}
.subscribe{margin-top:14px;display:inline-block;background:#8a8a8a;border-radius:2px;font-size:14px;padding:3px 7px}
.social{display:flex;align-items:center;gap:12px;font-size:14px;margin-bottom:12px}
.social i{width:26px;height:26px;border-radius:4px;background:#3f7fc2}
.footer-brand{left:816px;top:30px;width:242px;text-align:center;font-size:60px;font-weight:500;letter-spacing:6px;color:#fff}
.copy{left:816px;top:115px;width:242px;text-align:center;font-size:13px;line-height:19px;color:#eee}
</style>
</head>
<body>

<header class="site-header abs">
  <div class="brand abs"><span class="brand-mark"></span><span class="brand-name">QRV Advisors</span></div>
  <div class="phone abs">
    <svg width="26" height="26" viewBox="0 0 26 26"><circle cx="13" cy="13" r="11.5" fill="none" stroke="#777" stroke-width="2"/><path d="M9 7c-1 1-2 2-1 5s4 6 7 7 4 0 5-1l-2-3-2 1c-1 0-4-3-4-4l1-2z" fill="#777"/></svg>
    <span>555 014 2270</span>
  </div>
</header>

<nav class="main-nav abs">
  <ul class="nav-list">
    <li class="current">Home</li><li>About Us</li><li>Consulting Services</li><li>News &amp; Events</li><li>FAQ's</li><li>Contact Us</li>
  </ul>
  <div class="search abs">Search
    <svg width="16" height="16" viewBox="0 0 16 16"><circle cx="6.5" cy="6.5" r="4.5" fill="none" stroke="#fff" stroke-width="2"/><path d="M10 10l4 4" stroke="#fff" stroke-width="2.5"/></svg>
  </div>
</nav>

<section class="hero abs" role="img" aria-label="Photo of four business people smiling around a meeting table">
  <div class="hero-caption abs">QRV Services Are Offered By Industry Executives With Extensive M&amp;A Experience
    <div class="dots abs"><span class="on"></span><span></span><span></span><span></span><span></span></div>
  </div>
</section>

<div class="backdrop abs" role="img" aria-label="Blurred photo of parked truck fleets"></div>
<main class="content abs"></main>

<div class="services abs">
  <div class="service">
    <svg width="62" height="66" viewBox="0 0 62 66"><rect x="6" y="8" width="40" height="54" rx="3" fill="none" stroke="#666" stroke-width="3"/><rect x="12" y="3" width="40" height="54" rx="3" fill="#eee" stroke="#666" stroke-width="3"/><path d="M19 16h26M19 24h26M19 32h26M19 40h18" stroke="#666" stroke-width="3"/><path d="M34 46l7 7 16-16" fill="none" stroke="#666" stroke-width="4"/></svg>
    <span class="service-title">Bussiness<br>&amp; Planning</span>
  </div>
  <div class="service">
    <svg width="52" height="70" viewBox="0 0 52 70"><path d="M26 0L14 28h8v12L4 58v12h10V62l12-12 12 12v8h10V58L30 40V28h8z" fill="#555"/></svg>
    <span class="service-title">Mergers<br>&amp; Acquisition</span>
  </div>
  <div class="service">
    <svg width="68" height="68" viewBox="0 0 68 68"><circle cx="34" cy="34" r="31" fill="none" stroke="#666" stroke-width="4"/><circle cx="34" cy="34" r="24" fill="#f1f1f1" stroke="#666" stroke-width="2"/><path d="M24 22l14 22 6-2-14-22zM38 44l5 6 1-8" fill="none" stroke="#666" stroke-width="2.5"/></svg>
    <span class="service-title">Advisory<br>Services</span>
  </div>
</div>

<section class="box abs" style="left:121px">
  <h2 class="box-head">Our Mission</h2>
  <div class="mission-photo" role="img" aria-label="Group photo of a diverse professional team"></div>
  <p class="mission-text">Lorem Ipsum is simply dummy text of the printing and typesetting industry. Lorem Ipsum has been the industry's standard dummy text ever since the 1500sstandard dummy text ever since the 1500s dustry. Lorem ldustry. Lorem I dustry. Lorem.,</p>
  <span class="btn-dark">Read More</span>
</section>

<section class="box abs" style="left:440px">
  <h2 class="box-head">News &amp; Events</h2>
  <div class="news-item" style="top:42px"><div class="date"><b>APR</b>02</div><div><p class="news-title">Lorem ipsum dolor sit amet</p><p class="news-body">Lorem ipsum dol adipiscing elit, seder or sit amet, consectetu industry's standard dummy text ever er</p></div></div>
  <div class="news-item" style="top:129px"><div class="date"><b>APR</b>02</div><div><p class="news-title">Lorem ipsum dolor sit amet</p><p class="news-body">Lorem ipsum dol adipiscing elit, seder or sit amet, consectetu industry's standard dummy text ever er</p></div></div>
  <div class="news-item" style="top:218px"><div class="date"><b>APR</b>02</div><div><p class="news-title">Lorem ipsum dolor sit amet</p><p class="news-body">Lorem ipsum dol adipiscing elit, seder or sit amet, consectetu</p></div></div>
  <span class="btn-dark">Read More</span>
</section>

<section class="box abs" style="left:758px">
  <h2 class="box-head">Get in touch</h2>
  <span class="field" style="top:55px">Name</span><span class="input" style="top:44px"></span>
  <span class="field" style="top:99px">Phone</span><span class="input" style="top:89px"></span>
  <span class="field" style="top:143px">Email</span><span class="input" style="top:133px"></span>
  <span class="field" style="top:188px">Message</span><span class="input" style="top:177px;height:67px"></span>
  <span class="btn-dark">Submit</span>
</section>

<div class="partners abs">
  <span class="partner">Meridane</span>
  <span class="partner">Portwell Logistics</span>
  <span class="partner">Quickline Fleet</span>
  <span class="partner">Carpool Cove</span>
</div>
<svg class="arrow abs" style="left:137px" width="20" height="32" viewBox="0 0 20 32"><path d="M16 3L4 16l12 13" fill="none" stroke="#999" stroke-width="4"/></svg>
<svg class="arrow abs" style="left:1030px" width="20" height="32" viewBox="0 0 20 32"><path d="M4 3l12 13L4 29" fill="none" stroke="#999" stroke-width="4"/></svg>

<footer class="site-footer abs">
  <div class="f-col abs" style="left:137px;top:10px">
    <h3>Quick Links</h3>
    <ul><li>Home</li><li>About Us</li><li>Consulting Services</li><li>News &amp; Events</li><li>FAQ's</li><li>Contact Us</li></ul>
  </div>
  <div class="f-col abs" style="left:337px;top:10px;width:240px">
    <h3>Newsletter</h3>
    <p>Lorem Ipsum is simply dummy text of the printing and typesetting industry.</p>
    <div class="email">your e-mail address</div>
    <span class="subscribe">Subscribe</span>
  </div>
  <div class="f-col abs" style="left:636px;top:10px">
    <h3>Follow Us</h3>
    <div class="social"><i></i>Facenote</div>
    <div class="social"><i style="background:#4fa9e0"></i>Chirper</div>
    <div class="social"><i style="background:#2a7bb5"></i>Linkfolio</div>
  </div>
  <div class="footer-brand abs">QRV</div>
  <p class="copy abs">© 2014 QRVadvisors.<br>All Rights Reserved</p>
</footer>

</body>
</html>
```